Brochure for people who suffer from Sleep Apnea and need a medical device called a CPAP Machine

I want a brochure that can be placed in doctors offices with my competitors brochures. It needs to be bold and stand out and deliver a very strong message that draws the patients away from our competitors and to us. I have included a word document generally outlining some of my requirements and thoughts, please review prior to investing time into design!

Target Market(s)

people who suffer from sleep apnea, which is a disease that causes them to stop breathing many times per hour, resulting in the patient needing to wear a device called a CPAP Machine. This is an illness that can impact anyone but is more likely to impact those suffering from obesity and men.

Industry/Entity Type

Health Care

Other font styles liked:
• Use what you think is best

Colors

Designer to choose colors to be used in the design.

Requirements
Must have
• Please see word document for must have items, and feel free to contact me with any questions.
• Also must have bold colors, and/or graphics to really stand out among my competitors brochures.
Nice to have
• Would prefer to use the baby picture titled "sleeping baby 4" if possible but provided 2 other baby photos just in case. Whatever you want to add, use your professional creativity! You Don't need to use all the pictures uploaded!!!!!
Should not have
• Nothing discriminatory or offensive.

```html
<!DOCTYPE html>
<html lang="en">
<head>
<meta charset="utf-8">
<title>RestWell Direct – Sleep Therapy Brochure</title>
<link href="https://fonts.googleapis.com/css2?family=Montserrat:wght@600;700;800&family=Open+Sans:wght@400;600;700&display=swap" rel="stylesheet">
<style>
:root{
  --purple:#6b2a8c;
  --purple-dark:#4f1c69;
  --green:#2f9d57;
  --green-light:#48b86e;
  --gold:#e3b23c;
  --ink:#3a3a44;
  --paper:#ffffff;
  --backdrop:#e8e8ea;
}
*{box-sizing:border-box;margin:0;padding:0}
html,body{width:1200px;height:2400px;overflow:hidden}
body{background:var(--backdrop);font-family:"Open Sans",Arial,sans-serif;color:var(--ink);position:relative}
.spread{position:absolute;left:50px;width:1100px;height:850px;display:flex;background:var(--paper);box-shadow:0 10px 30px rgba(0,0,0,.12)}
.spread--outside{top:150px}
.spread--inside{top:1400px}
.panel{position:relative;width:366.67px;height:100%;overflow:hidden}
.panel + .panel{border-left:1px solid rgba(0,0,0,.06)}
.photo{position:absolute;left:0;width:100%}
.brand{display:flex;align-items:center;gap:10px;font-family:"Montserrat",Arial,sans-serif;font-weight:700;font-size:24px;color:var(--purple)}
.brand__dot{width:16px;height:16px;border-radius:50%;background:var(--green)}
.brand--light{color:#fff}
.brand--light .brand__dot{background:#fff}
h2{font-family:"Montserrat",Arial,sans-serif;font-weight:800;letter-spacing:.5px}
.curve{position:absolute;left:0;width:100%}

/* features flap */
.features .photo{top:0;height:290px;background:linear-gradient(135deg,#d9cbe3,#f1e6dc 60%,#c9b4d6)}
.features h2{position:absolute;top:320px;left:32px;font-size:24px;color:var(--purple)}
.feature-list{position:absolute;top:375px;left:32px;right:28px;list-style:none}
.feature-list li{display:flex;align-items:center;gap:14px;font-size:16px;font-weight:600;margin-bottom:22px}
.feature-list svg{flex:none}
.features .foot{position:absolute;bottom:0;left:0;right:0;height:40px;background:var(--purple)}

/* back panel */
.back{background:linear-gradient(180deg,var(--green-light),var(--green))}
.back .brand{position:absolute;top:70px;left:0;right:0;justify-content:center;font-size:26px}
.back .tagline{position:absolute;top:115px;width:100%;text-align:center;color:#fff;font-size:15px;font-weight:600}
.back .photo{top:160px;left:83px;width:200px;height:200px;border-radius:50%;border:6px solid #fff;background:linear-gradient(135deg,#c8d7e6,#e6eef5)}
.back .seal{position:absolute;top:390px;left:143px;width:80px;height:80px;border-radius:50%;background:var(--gold)}
.back .call{position:absolute;top:510px;left:0;right:0;display:flex;justify-content:center;align-items:center;gap:10px;color:#fff;font-family:"Montserrat",Arial,sans-serif;font-weight:700;font-size:24px}
.back .web{position:absolute;top:555px;width:100%;text-align:center;color:#fff;font-size:16px}
.back .ribbon{position:absolute;bottom:0;left:0;right:0;height:110px;background:var(--purple);color:#fff;display:flex;align-items:flex-end;justify-content:center;padding-bottom:30px;font-family:"Montserrat",Arial,sans-serif;font-weight:700;font-style:italic;font-size:18px}

/* cover */
.cover .brand{position:absolute;top:40px;right:34px}
.cover .headline{position:absolute;top:134px;left:34px;right:30px;display:flex;flex-direction:column;gap:12px}
.cover h2{font-size:33px;line-height:1.1;color:var(--purple)}
.cover .sub{font-size:20px;font-weight:700;color:var(--green);font-style:italic;line-height:1.2}
.cover .photo{top:318px;height:292px;background:linear-gradient(135deg,#f3ddd0,#fbeee6 55%,#e9d2c5)}
.cover .ribbon{position:absolute;top:630px;left:0;right:0;height:60px;background:var(--purple);color:#fff;display:flex;align-items:center;justify-content:center;font-family:"Montserrat",Arial,sans-serif;font-weight:700;font-style:italic;font-size:19px}
.cover .call{position:absolute;top:720px;left:58px;right:58px;height:54px;border-radius:27px;background:var(--green);color:#fff;display:flex;align-items:center;justify-content:center;gap:10px;font-family:"Montserrat",Arial,sans-serif;font-weight:700;font-size:21px}

/* inside left */
.about .top{position:absolute;top:0;left:0;right:0;height:520px;background:var(--purple);color:#fff;padding:60px 32px 0}
.about h2{font-size:24px;margin-bottom:24px}
.about ul{list-style:none}
.about li{display:flex;gap:12px;align-items:center;font-size:15px;margin-bottom:16px}
.about li::before{content:"";width:10px;height:10px;border-radius:50%;background:var(--green-light);flex:none}
.about p{font-size:15px;line-height:1.55;margin-top:20px}
.about .photo{top:520px;height:330px;background:linear-gradient(135deg,#cdd3da,#eef0f3 60%,#b9c1ca)}

/* inside middle */
.help{padding:70px 34px 0}
.help h2{font-size:26px;color:var(--purple);text-align:center;margin-bottom:36px}
.help-item{display:flex;gap:16px;align-items:flex-start;margin-bottom:36px}
.help-item svg{flex:none}
.help-item p{font-size:15px;line-height:1.55}

/* inside right */
.start .photo{top:0;height:360px;background:linear-gradient(135deg,#c9d9e8,#eaf1f7 60%,#b8c9da)}
.start h2{position:absolute;top:395px;left:32px;right:32px;font-size:24px;color:var(--purple);line-height:1.2}
.start p{position:absolute;top:480px;left:32px;right:32px;font-size:15px;line-height:1.6}
.start .bottom{position:absolute;bottom:0;left:0;right:0;height:170px;background:var(--purple)}
.start .call{position:absolute;bottom:50px;left:0;right:0;display:flex;justify-content:center;align-items:center;gap:10px;color:#fff;font-family:"Montserrat",Arial,sans-serif;font-weight:700;font-size:24px}
</style>
</head>
<body>

<section class="spread spread--outside">
  <article class="panel features">
    <div class="photo" role="img" aria-label="Photo of a couple sleeping peacefully in bed"></div>
    <svg class="curve" style="top:250px" width="367" height="50" viewBox="0 0 367 50"><path d="M0 40 Q180 0 367 20 L367 50 L0 50Z" fill="#fff"/></svg>
    <h2>Why Choose Us</h2>
    <ul class="feature-list">
      <li><svg width="34" height="34" viewBox="0 0 34 34"><circle cx="17" cy="17" r="17" fill="#6b2a8c"/><path d="M10 17l5 5 9-10" stroke="#fff" stroke-width="3" fill="none"/></svg>Free home delivery</li>
      <li><svg width="34" height="34" viewBox="0 0 34 34"><circle cx="17" cy="17" r="17" fill="#6b2a8c"/><path d="M10 17l5 5 9-10" stroke="#fff" stroke-width="3" fill="none"/></svg>Mask fitting by experts</li>
      <li><svg width="34" height="34" viewBox="0 0 34 34"><circle cx="17" cy="17" r="17" fill="#6b2a8c"/><path d="M10 17l5 5 9-10" stroke="#fff" stroke-width="3" fill="none"/></svg>Insurance billing handled</li>
      <li><svg width="34" height="34" viewBox="0 0 34 34"><circle cx="17" cy="17" r="17" fill="#6b2a8c"/><path d="M10 17l5 5 9-10" stroke="#fff" stroke-width="3" fill="none"/></svg>Supplies shipped on schedule</li>
      <li><svg width="34" height="34" viewBox="0 0 34 34"><circle cx="17" cy="17" r="17" fill="#6b2a8c"/><path d="M10 17l5 5 9-10" stroke="#fff" stroke-width="3" fill="none"/></svg>Support seven days a week</li>
      <li><svg width="34" height="34" viewBox="0 0 34 34"><circle cx="17" cy="17" r="17" fill="#6b2a8c"/><path d="M10 17l5 5 9-10" stroke="#fff" stroke-width="3" fill="none"/></svg>No waiting rooms</li>
    </ul>
    <div class="foot"></div>
  </article>

  <article class="panel back">
    <svg class="curve" style="top:0" width="367" height="60" viewBox="0 0 367 60"><path d="M0 0 L367 0 L367 20 Q180 70 0 30Z" fill="#6b2a8c"/></svg>
    <div class="brand brand--light"><span class="brand__dot"></span>RestWell Direct</div>
    <div class="tagline">Your Sleep Therapy Partner</div>
    <div class="photo" role="img" aria-label="Photo of a patient resting comfortably with a CPAP mask"></div>
    <div class="seal" role="img" aria-label="Quality seal"></div>
    <div class="call"><svg width="22" height="22" viewBox="0 0 24 24"><path d="M6.6 10.8a15 15 0 006.6 6.6l2.2-2.2a1 1 0 011-.25 11.4 11.4 0 003.6.57 1 1 0 011 1V20a1 1 0 01-1 1A17 17 0 013 4a1 1 0 011-1h3.5a1 1 0 011 1c0 1.25.2 2.45.57 3.6a1 1 0 01-.25 1z" fill="#fff"/></svg>(555) 014-2200</div>
    <div class="web">restwelldirect.com</div>
    <div class="ribbon">We Bring The Store To You</div>
  </article>

  <article class="panel cover">
    <div class="brand"><span class="brand__dot"></span>RestWell Direct</div>
    <svg class="curve" style="top:92px" width="367" height="30" viewBox="0 0 367 30"><path d="M0 22 Q180 -6 367 14" stroke="#6b2a8c" stroke-width="5" fill="none"/><path d="M0 28 Q180 4 367 22" stroke="#2f9d57" stroke-width="3" fill="none"/></svg>
    <div class="headline">
      <h2>WANT SLEEP LIKE A BABY AGAIN?</h2>
      <div class="sub">Let us show you how!</div>
    </div>
    <div class="photo" role="img" aria-label="Photo of a sleeping baby"></div>
    <div class="ribbon">We Bring The Store To You</div>
    <div class="call"><svg width="20" height="20" viewBox="0 0 24 24"><path d="M6.6 10.8a15 15 0 006.6 6.6l2.2-2.2a1 1 0 011-.25 11.4 11.4 0 003.6.57 1 1 0 011 1V20a1 1 0 01-1 1A17 17 0 013 4a1 1 0 011-1h3.5a1 1 0 011 1c0 1.25.2 2.45.57 3.6a1 1 0 01-.25 1z" fill="#fff"/></svg>(555) 014-2200</div>
  </article>
</section>

<section class="spread spread--inside">
  <article class="panel about">
    <div class="top">
      <h2>What Is Sleep Apnea?</h2>
      <ul>
        <li>Breathing stops many times an hour</li>
        <li>Loud snoring and restless nights</li>
        <li>Daytime fatigue and headaches</li>
        <li>Higher risk for heart problems</li>
      </ul>
      <p>A CPAP machine keeps your airway open so you wake up rested.</p>
    </div>
    <div class="photo" role="img" aria-label="Photo of CPAP equipment with mask and tubing"></div>
  </article>

  <article class="panel help">
    <h2>How We Help</h2>
    <div class="help-item"><svg width="30" height="30" viewBox="0 0 30 30"><circle cx="15" cy="15" r="15" fill="#2f9d57"/><path d="M9 15l4 4 8-9" stroke="#fff" stroke-width="3" fill="none"/></svg><p>We deliver your CPAP machine and supplies straight to your door.</p></div>
    <div class="help-item"><svg width="30" height="30" viewBox="0 0 30 30"><circle cx="15" cy="15" r="15" fill="#2f9d57"/><path d="M9 15l4 4 8-9" stroke="#fff" stroke-width="3" fill="none"/></svg><p>Our team fits your mask so therapy feels comfortable from night one.</p></div>
    <div class="help-item"><svg width="30" height="30" viewBox="0 0 30 30"><circle cx="15" cy="15" r="15" fill="#2f9d57"/><path d="M9 15l4 4 8-9" stroke="#fff" stroke-width="3" fill="none"/></svg><p>We work with your insurance and handle the paperwork for you.</p></div>
    <div class="help-item"><svg width="30" height="30" viewBox="0 0 30 30"><circle cx="15" cy="15" r="15" fill="#2f9d57"/><path d="M9 15l4 4 8-9" stroke="#fff" stroke-width="3" fill="none"/></svg><p>Reorder reminders keep fresh filters and cushions arriving on time.</p></div>
  </article>

  <article class="panel start">
    <div class="photo" role="img" aria-label="Photo of a man wearing a CPAP mask"></div>
    <h2>Sleep Better Starting Tonight</h2>
    <p>Call today and speak with a sleep specialist who will guide you through every step of your therapy.</p>
    <svg class="curve" style="bottom:165px" width="367" height="50" viewBox="0 0 367 50"><path d="M0 50 Q190 0 367 30 L367 50Z" fill="#6b2a8c"/></svg>
    <div class="bottom"></div>
    <div class="call"><svg width="22" height="22" viewBox="0 0 24 24"><path d="M6.6 10.8a15 15 0 006.6 6.6l2.2-2.2a1 1 0 011-.25 11.4 11.4 0 003.6.57 1 1 0 011 1V20a1 1 0 01-1 1A17 17 0 013 4a1 1 0 011-1h3.5a1 1 0 011 1c0 1.25.2 2.45.57 3.6a1 1 0 01-.25 1z" fill="#fff"/></svg>(555) 014-2200</div>
  </article>
</section>

</body>
</html>
```